Vellmore Family Law, legal technician needs a website and design

I need a website for a family law practice. I specialize in collaborative law, unbundled services, and mediation. The website must contain my company logo (file attached), and the website must be a mixture of my personality and my profession. I have attached additional information to explain my personality and profession.

Target Market(s)

Lower through middle-class (income level up to $200,000 per year)

Coding

Coded - Design and coding required

Number of Pages Required

1 page

Requirements
Must have
• Must have enough pages to cover required content. I submitted below some content about the collaborative law process. All of the content is not necessary. However, the website must have enough content to clearly describe the services I offer. Use your professionalism and judgment regarding font, font size, etc.

```html
<!DOCTYPE html>
<html lang="en">
<head>
<meta charset="utf-8">
<title>Vellmore Family Law</title>
<link href="https://fonts.googleapis.com/css2?family=Cinzel:wght@500;600;700&family=Montserrat:wght@400;500;600;700&display=swap" rel="stylesheet">
<style>
:root{
  --navy:#0c0c2a;
  --navy-2:#1b1b45;
  --gold:#b8b23c;
  --gold-light:#cfc852;
  --gold-dark:#8c872a;
  --gold-grad:linear-gradient(90deg,#cbc64e,#8f8a2b);
  --white:#ffffff;
  --paper:#f5f5f5;
  --ink:#1d1d2e;
  --muted:#444455;
  --dots:#8f8f9a;
}
*{box-sizing:border-box;margin:0;padding:0}
html,body{width:1200px;height:5329px;overflow:hidden}
body{font-family:'Montserrat',sans-serif;color:var(--ink);background:var(--white)}
.page{position:relative;width:1200px;height:5329px;overflow:hidden}
.abs{position:absolute}
.serif{font-family:'Cinzel',serif}

.topbar{left:0;top:0;width:1200px;height:52px;background:var(--gold-grad);color:var(--white);font-size:11px;font-weight:600;display:flex;align-items:center;justify-content:center}
.header{left:0;top:52px;width:1200px;height:118px;background:var(--white)}
.brand{display:flex;align-items:center;gap:14px}
.brand-mark{width:18px;height:18px;background:var(--gold)}
.brand-name{font-family:'Cinzel',serif;font-weight:600;color:var(--gold);font-size:22px;line-height:1.05}
.nav{left:456px;top:100px;display:flex;gap:16px;font-size:11.5px;font-weight:700;color:var(--navy)}
.phone-pill{left:830px;top:82px;width:198px;height:58px;border-radius:29px;background:var(--gold-grad);display:flex;align-items:center;gap:12px;padding-left:8px;color:var(--white);font-weight:700;font-size:15px}
.icon-circle{width:42px;height:42px;border-radius:50%;background:var(--gold-light);display:flex;align-items:center;justify-content:center;border:2px solid rgba(255,255,255,.5)}

.hero-photo{left:0;top:170px;width:1200px;height:688px;background:linear-gradient(180deg,#c9ccd6 0%,#e8e9ee 45%,#d7d8dc 100%)}
.hero-people{left:60px;top:330px;width:720px;height:528px;background:linear-gradient(180deg,#4a4a55 0%,#1d1d25 100%);border-radius:220px 220px 0 0;opacity:.85}
.hero-title{right:120px;top:495px;text-align:right;font-family:'Cinzel',serif;font-weight:600;font-size:62px;line-height:1.1;color:var(--navy)}
.hero-band{left:0;top:858px;width:1200px;height:37px;background:var(--gold-grad)}
.dots{left:570px;top:872px;display:flex;gap:8px}
.dots span{width:11px;height:11px;border-radius:50%;background:#d7d5a0}
.dots span.on{background:var(--navy)}

.dark{background:var(--navy);color:var(--white)}
.sec-what{left:0;top:895px;width:1200px;height:620px}
.sec-collab{left:0;top:1515px;width:1200px;height:767px;background:var(--white)}
.sec-why{left:0;top:2282px;width:1200px;height:691px}
.sec-benefits{left:0;top:2973px;width:1200px;height:911px;background:var(--paper)}
.sec-blog{left:0;top:3884px;width:1200px;height:811px;background:var(--white)}
.footer{left:0;top:4695px;width:1200px;height:634px}

.h-gold{font-family:'Cinzel',serif;font-weight:600;color:var(--gold);font-size:38px;letter-spacing:1px}
.h-center{left:0;width:1200px;display:flex;align-items:center;justify-content:center;gap:22px}
.h-center::before,.h-center::after{content:"";width:64px;height:3px;background:var(--gold)}
.body-text{font-size:11.5px;line-height:27px}
.btn{display:inline-flex;align-items:center;justify-content:center;height:50px;padding:0 20px;border-radius:25px;background:var(--gold-grad);color:var(--navy);font-family:'Cinzel',serif;font-weight:700;font-size:13.5px;letter-spacing:.5px}
.btn.sm{height:38px;font-size:11px;padding:0 14px;border-radius:19px}

.step{width:52px;height:128px;border-radius:8px;background:var(--gold-grad);color:var(--white);font-weight:700;font-size:24px;display:flex;align-items:center;justify-content:center}
.step span{transform:rotate(-90deg);white-space:nowrap}
.dl-v{width:0;border-left:2px dotted var(--dots)}
.dl-h{height:0;border-top:2px dotted var(--dots)}

.reason{width:200px;text-align:center}
.ring{width:192px;height:192px;border-radius:50%;margin:0 auto;position:relative;display:flex;flex-direction:column;align-items:center;justify-content:center;gap:10px}
.ring.outline{border:5px solid var(--gold)}
.ring.filled{background:var(--gold-grad);border:5px solid var(--gold)}
.ring-label{font-size:12.5px;font-weight:600;line-height:18px;color:var(--gold)}
.ring.filled .ring-label{color:var(--white)}
.badge{position:absolute;right:-6px;top:-24px;width:62px;height:62px;border-radius:50%;background:var(--gold);border:4px solid var(--navy);color:var(--white);font-size:28px;font-weight:600;display:flex;align-items:center;justify-content:center}
.reason p{font-size:10.5px;line-height:20px;margin-top:22px;color:var(--white)}

.service{width:400px;height:292px;background:var(--navy)}
.service .photo{width:400px;height:240px}
.service .label{height:52px;display:flex;align-items:center;padding:0 16px;color:var(--white);font-weight:700;font-size:19px;letter-spacing:.5px}
.service.right .label{justify-content:flex-end}
.seal{left:480px;top:3352px;width:240px;height:240px;border-radius:50%;background:var(--white);display:flex;align-items:center;justify-content:center;font-family:'Cinzel',serif;font-weight:600;font-size:26px;color:var(--gold);text-align:center;line-height:1.15}

.post{border:1px solid #c9c9d2;background:var(--white)}
.post h3{font-family:'Montserrat',sans-serif;font-weight:700;font-size:16px;color:var(--navy)}
.post p{font-size:11px;line-height:20px;color:var(--muted)}
.post-side{display:flex;width:388px;height:225px}
.post-side .photo{width:157px;height:100%;flex:none}
.post-side .txt{padding:16px 14px}
.post-side p{text-align:justify}

.cta{left:172px;top:4645px;width:856px;height:100px;border-radius:24px;background:var(--gold-grad);display:flex;align-items:center;justify-content:space-between;padding:0 20px 0 22px}
.cta-text{color:var(--white);font-weight:600;font-size:15.5px;line-height:27px}
.pill{height:52px;border-radius:26px;display:inline-flex;align-items:center;justify-content:center;font-family:'Cinzel',serif;font-weight:700;font-size:14px;padding:0 24px}
.pill.navy{background:var(--navy);color:var(--white)}
.pill.light{background:var(--white);color:var(--navy);margin-left:10px}

.field{background:var(--white);border-radius:22px;height:46px;font-size:12px;color:#555;padding:0 14px;display:flex;align-items:center}
.contact-line{display:flex;align-items:center;gap:16px}
.contact-line .icon-circle{background:var(--gold);border:none}
.contact-line small{display:block;font-size:11px;font-weight:500}
.contact-line strong{font-size:18px;font-weight:700}
.copyright{left:172px;top:5240px;width:856px;height:66px;border-radius:33px;background:var(--gold-grad);color:var(--white);font-size:13px;display:flex;align-items:center;justify-content:center}
</style>
</head>
<body>
<div class="page">

  <div class="abs topbar">Vellmore Family Law, collaborative law and unbundled legal services in King County, Washington state</div>

  <header class="abs header">
    <div class="abs brand" style="left:172px;top:26px">
      <div class="brand-mark"></div>
      <div class="brand-name">VELLMORE<br>FAMILY LAW</div>
    </div>
  </header>
  <nav class="abs nav"><span>HOME</span><span>ABOUT</span><span>BENEFITS</span><span>FEATURES</span><span>BLOG</span><span>CONTACT</span></nav>
  <div class="abs phone-pill">
    <div class="icon-circle"><svg width="20" height="20" viewBox="0 0 24 24" fill="none" stroke="#fff" stroke-width="2"><path d="M5 3h4l2 5-3 2a12 12 0 0 0 6 6l2-3 5 2v4a2 2 0 0 1-2 2A17 17 0 0 1 3 5a2 2 0 0 1 2-2z"/></svg></div>
    + 120 555 0148
  </div>

  <section>
    <div class="abs hero-photo" role="img" aria-label="City skyline with a tall observation tower in soft daylight"></div>
    <div class="abs hero-people" role="img" aria-label="Three attorneys in dark business suits standing with arms crossed"></div>
    <h1 class="abs hero-title">VELLMORE<br>FAMILY<br>LAW</h1>
    <div class="abs hero-band"></div>
    <div class="abs dots"><span class="on"></span><span></span><span></span></div>
  </section>

  <section class="abs dark sec-what">
    <h2 class="abs h-gold" style="left:172px;top:92px;display:flex;align-items:center;gap:22px">WHAT I DO <span style="width:64px;height:3px;background:var(--gold);display:block"></span></h2>
    <p class="abs body-text" style="left:172px;top:165px;width:478px;text-align:justify">Simply trusting in the process, however, is not enough. The process of divorcing, separating households and finances, and coming up with a parenting plan for the children is hard work. If you do not trust it the process will be harder to get through. Trust in the process will make it easier to address the tough issues that will happen in the process because the goal of achieving that better personal result remains in focus.</p>
    <a class="abs btn" style="left:172px;top:355px">READ MORE</a>
    <div class="abs" role="img" aria-label="Three attorneys framed against a large gold panel" style="left:683px;top:105px;width:327px;height:335px;border-radius:26px;background:linear-gradient(135deg,#c9c24a,#8f8a2a)"></div>
  </section>

  <section class="abs sec-collab">
    <h2 class="abs h-gold h-center" style="top:72px">COLLABORATIVE LAW PROCESS</h2>
    <p class="abs body-text" style="left:170px;top:148px;width:860px;text-align:center;line-height:24px">Every year, hundreds of thousands of marriages end in divorce. Are you in this situation right now? Are you getting ready to hire a lawyer to help you with your case?<br>If so, before you make a decision on the process you are choosing for your divorce process, read on to learn more about the Collaborative approach to divorce and you will discover the benefits this process offers. When you are done reading this post you will see why so many divorcing couples choose the Collaborative process for their divorce.</p>
    <h3 class="abs" style="left:172px;top:325px;font-size:16px;font-weight:700;color:var(--navy)">WHAT IS COLLABORATIVE PRACTICE?</h3>
    <p class="abs body-text" style="left:172px;top:362px;width:425px;text-align:justify">Collaborate practice is a process where trained professionals, including attorneys, help couples resolve their disputes without litigation and outside of court. Instead, those involved in the case approach the legal process through the lens of teamwork, trouble-shooting, and problem solving rather than fighting to "beat" someone else. Another way of describing this process is rather than looking at a "win - lose" result, see it as a "win-win" for all involved.<br>Essential to the Collaborative law methodology is the fact that both parties retain separate attorneys.</p>
    <a class="abs btn" style="left:172px;top:617px">READ MORE</a>
    <div class="abs" style="left:635px;top:342px;width:390px;height:328px;border-left:4px solid var(--gold);border-bottom:4px solid var(--gold)"></div>
    <div class="abs" role="img" aria-label="Video still of two women talking across a desk in a bright office" style="left:657px;top:325px;width:371px;height:335px;background:linear-gradient(135deg,#7a889c,#c7ccd4 60%,#4b5568)"></div>
    <svg class="abs" style="left:815px;top:465px" width="56" height="56" viewBox="0 0 56 56"><circle cx="28" cy="28" r="25" fill="none" stroke="#fff" stroke-width="3"/><path d="M22 17l17 11-17 11z" fill="#fff"/></svg>
  </section>

  <section class="abs dark sec-why">
    <h2 class="abs serif" style="left:0;top:70px;width:1200px;text-align:center;color:var(--gold);font-size:26px;font-weight:600;line-height:35px">WHY DO PEOPLE CHOOSE A COLLABORATIVE<br>DIVORCE PROCESS?</h2>
    <p class="abs" style="left:200px;top:158px;width:800px;text-align:center;font-size:11.5px;line-height:27px">There are lots of reasons why people choose the Collaborative process and hire a Collaborative attorney to assist them, including the following.</p>

    <div class="abs reason" style="left:168px;top:305px">
      <div class="ring outline">
        <div class="badge">01</div>
        <svg width="52" height="48" viewBox="0 0 52 48" fill="none" stroke="#b8b23c" stroke-width="3" stroke-linejoin="round"><path d="M26 44L7 25a11 11 0 0 1 19-14a11 11 0 0 1 19 14z"/></svg>
        <div class="ring-label">Children<br>First</div>
      </div>
      <p>How many times have you talked to someone who is a child of a contentious divorce, or seen a friend or family member</p>
    </div>
    <div class="abs reason" style="left:390px;top:305px">
      <div class="ring filled">
        <div class="badge" style="background:var(--navy);border-color:var(--gold)">02</div>
        <svg width="44" height="50" viewBox="0 0 44 50" fill="none" stroke="#fff" stroke-width="3"><path d="M22 3l18 7v14c0 12-8 20-18 23C12 44 4 36 4 24V10z"/><path d="M14 25l6 6 11-12"/></svg>
        <div class="ring-label">Privacy &amp;<br>Confidentiality</div>
      </div>
      <p>The Collaborative process is a confidential process, with a lot more privacy than the traditional divorce process</p>
    </div>
    <div class="abs reason" style="left:610px;top:305px">
      <div class="ring outline">
        <div class="badge">03</div>
        <svg width="46" height="52" viewBox="0 0 46 52" fill="none" stroke="#b8b23c" stroke-width="3"><circle cx="23" cy="30" r="18"/><path d="M17 4h12M23 4v8M23 30l8-7"/></svg>
        <div class="ring-label">Increased<br>Efficiency</div>
      </div>
      <p>Collaborative cases often get wrapped up much faster than traditional legal cases. It's not uncommon for divorce cases</p>
    </div>
    <div class="abs reason" style="left:830px;top:305px">
      <div class="ring filled">
        <div class="badge" style="background:var(--navy);border-color:var(--gold)">04</div>
        <svg width="50" height="50" viewBox="0 0 50 50" fill="none" stroke="#fff" stroke-width="3"><circle cx="25" cy="25" r="21"/><path d="M31 17c-2-2-12-3-12 3s12 4 12 10-10 5-13 2M25 11v28"/></svg>
        <div class="ring-label">Lower Costs /<br>Higher Rewards</div>
      </div>
      <p>Finally, a Collaborative approach is typically much more cost-effective than other legal approaches. This may be counter-intuitive</p>
    </div>
  </section>

  <section class="abs sec-benefits">
    <h2 class="abs h-gold h-center" style="top:70px">BENEFITS OF WHAT I DO</h2>
  </section>
  <div class="abs service" style="left:172px;top:3153px">
    <div class="photo" role="img" aria-label="Smiling businesswoman shaking hands across a desk" style="background:linear-gradient(135deg,#8a93a3,#dfe2e7 55%,#5f6678)"></div>
    <div class="label">COLLABORATIVE LAW</div>
  </div>
  <div class="abs service right" style="left:628px;top:3153px">
    <div class="photo" role="img" aria-label="Stacks of legal documents beside a balance scale on a desk" style="background:linear-gradient(135deg,#4d4f57,#c8c6bd 55%,#a8a592)"></div>
    <div class="label">UNBUNDLED SERVICES</div>
  </div>
  <div class="abs service" style="left:172px;top:3500px">
    <div class="photo" role="img" aria-label="Mediator speaking with a client at a table" style="background:linear-gradient(135deg,#c9c2b8,#e9e5df 50%,#3e3a3a)"></div>
    <div class="label">MEDIATION</div>
  </div>
  <div class="abs service right" style="left:628px;top:3500px">
    <div class="photo" role="img" aria-label="Smiling attorney seated at a desk in a warm office" style="background:linear-gradient(135deg,#8c6a4e,#d8c9b4 55%,#57402f)"></div>
    <div class="label">FAMILY LAW</div>
  </div>
  <div class="abs seal">Vellmore<br>Family Law</div>

  <section class="abs sec-blog">
    <h2 class="abs h-gold h-center" style="top:72px">BLOG POSTS</h2>
  </section>
  <article class="abs post" style="left:172px;top:4047px;width:444px;height:488px">
    <div role="img" aria-label="Team meeting around a table in a bright office" style="height:262px;background:linear-gradient(135deg,#cfd3d8,#f1f2f3 50%,#8d8f95)"></div>
    <h3 style="text-align:center;margin-top:26px">ULLAM CORPORIS SUSCIPIT</h3>
    <p style="text-align:center;width:400px;margin:12px auto 0">Sed ut perspiciatis unde omnis iste natus error sit voluptatem accus antium doloremquem totam rem aperiam, Eaque ipsa quae ab illo inventore veritatis et quasi architecto.</p>
    <div style="text-align:center;margin-top:14px"><a class="btn" style="height:46px">READ MORE</a></div>
  </article>
  <article class="abs post post-side" style="left:640px;top:4047px">
    <div class="photo" role="img" aria-label="Portrait of a smiling woman in business attire" style="background:linear-gradient(180deg,#9d9588,#3d3530)"></div>
    <div class="txt">
      <h3>CORPORIS SUSCIPIT</h3>
      <p style="margin-top:10px">Sed ut perspiciatis unde omnis iste natus error sit voluptatem accus antium beatae vitae dicta sunt explicaboe.</p>
      <a class="btn sm" style="margin-top:14px">READ MORE</a>
    </div>
  </article>
  <article class="abs post post-side" style="left:640px;top:4310px">
    <div class="photo" role="img" aria-label="Portrait of a young woman in a blazer" style="background:linear-gradient(180deg,#8f8578,#2f2925)"></div>
    <div class="txt">
      <h3>CORPORIS SUSCIPIT</h3>
      <p style="margin-top:10px">Sed ut perspiciatis unde omnis iste natus error sit voluptatem accus antium beatae vitae dicta sunt explicaboe.</p>
      <a class="btn sm" style="margin-top:14px">READ MORE</a>
    </div>
  </article>

  <footer class="abs dark footer">
    <div class="abs brand" style="left:172px;top:175px">
      <div class="brand-mark"></div>
      <div class="brand-name" style="font-size:26px">VELLMORE<br>FAMILY LAW</div>
    </div>
    <div class="abs contact-line" style="left:172px;top:300px">
      <div class="icon-circle"><svg width="20" height="20" viewBox="0 0 24 24" fill="none" stroke="#fff" stroke-width="2"><path d="M5 3h4l2 5-3 2a12 12 0 0 0 6 6l2-3 5 2v4a2 2 0 0 1-2 2A17 17 0 0 1 3 5a2 2 0 0 1 2-2z"/></svg></div>
      <div><small>CALL US AT:</small><strong>+ 120 555 0193</strong></div>
    </div>
    <div class="abs contact-line" style="left:172px;top:385px">
      <div class="icon-circle"><svg width="20" height="20" viewBox="0 0 24 24" fill="none" stroke="#fff" stroke-width="2"><rect x="3" y="5" width="18" height="14" rx="2"/><path d="M3 7l9 6 9-6"/></svg></div>
      <div><small>MAIL US AT:</small><strong>hello@vellmorelaw.com</strong></div>
    </div>
    <h2 class="abs serif" style="left:528px;top:138px;color:var(--gold);font-size:28px;font-weight:600">CONTACT US</h2>
    <div class="abs field" style="left:528px;top:195px;width:244px">First Name</div>
    <div class="abs field" style="left:784px;top:195px;width:244px">Last Name</div>
    <div class="abs field" style="left:528px;top:256px;width:244px">Email</div>
    <div class="abs field" style="left:784px;top:256px;width:244px">Phone</div>
    <div class="abs field" style="left:528px;top:316px;width:500px;height:92px;align-items:flex-start;padding-top:14px;border-radius:24px">Message</div>
    <a class="abs btn" style="left:528px;top:430px;width:128px">SUBMIT</a>
  </footer>

  <div class="abs cta">
    <div class="cta-text">Vellmore Family Law, collaborative law and unbundled legal<br>services in King County, Washington state</div>
    <div><span class="pill navy">NEXT STEP</span><span class="pill light">CONTACT US</span></div>
  </div>

  <div class="abs copyright">Copyrights @ 2021 Vellmore Family Law. All Rights Reserved.</div>

  <div class="abs dl-v" style="left:82px;top:1266px;height:170px"></div>
  <div class="abs dl-h" style="left:82px;top:1436px;width:1020px"></div>
  <div class="abs dl-v" style="left:1100px;top:1436px;height:384px"></div>
  <div class="abs dl-v" style="left:1100px;top:1945px;height:300px"></div>
  <div class="abs dl-h" style="left:82px;top:2245px;width:1020px"></div>
  <div class="abs dl-v" style="left:82px;top:2245px;height:380px"></div>
  <div class="abs dl-v" style="left:82px;top:2755px;height:180px"></div>
  <div class="abs dl-h" style="left:82px;top:2935px;width:1020px"></div>
  <div class="abs dl-v" style="left:1100px;top:2935px;height:405px"></div>
  <div class="abs dl-v" style="left:1100px;top:3465px;height:380px"></div>
  <div class="abs dl-h" style="left:82px;top:3845px;width:1020px"></div>
  <div class="abs dl-v" style="left:82px;top:3845px;height:370px"></div>
  <div class="abs dl-v" style="left:82px;top:4345px;height:370px"></div>
  <div class="abs" style="left:73px;top:4712px;width:20px;height:20px;border-radius:50%;background:var(--gold)"></div>

  <div class="abs step" style="left:56px;top:1138px"><span>Step 1</span></div>
  <div class="abs step" style="left:1074px;top:1820px"><span>Step 2</span></div>
  <div class="abs step" style="left:56px;top:2625px"><span>Step 3</span></div>
  <div class="abs step" style="left:1074px;top:3340px"><span>Step 4</span></div>
  <div class="abs step" style="left:56px;top:4215px"><span>Step 5</span></div>

</div>
</body>
</html>
```